Need A Label For An Energy Drink/Nootropic Supplement!

For this Guaranteed Project, we need a label design for Vexar Energy; a powdered energy drink designed for video gamers. Make your mark on this growing industry!
Our product is zero calorie, no sugar, powdered, mixes in water with a shaker bottle, and provides both energy AND nootropics that stimulate the brain for better focus and more mental clarity.
Our biggest competitor and a product to reference is K Blaze (https://kblazemix.com/collections/tubs).

Our target market = video gamers, males, age 16-35.
We are launching with 2 flavors (Pink Lemonade and Mixed Berry).
We want the label to be masculine. We want to be a bit "edgier", more like Drevik Energy.

The container is a black, powdered pre-workout sized plastic tub with smooth top (see this link https://kblazemix.com/collections/tubs/products/nixplum-tub-free-3-pack).

I've attached some examples of cool labels. Also attached our company logo. The project is GUARANTEED! Thank you and good luck!

Target Market(s)

Male video gamers ages 16-35

Industry/Entity Type

Supplement

Font styles to use
Sans Serif

Requirements
Must have
• Vexar Energy logo nice and prominent. Then the flavor of the drink below that (use Pink Lemonade).
• Also on the front "Zero Calories" and "No Sugar" and our slogan "The Most Powerful Energy Drink In Gaming" with the TM trademark sign.
• Also say "30 servings".
• Finally, at the bottom of the front panel "Dietary Supplement / Net Wt. 0.0oz (000g)"
• We will share the "nitty gritty" things like ingredients and warnings if we select your project.
Nice to have
• masculine feel, edgier design

```html
<!DOCTYPE html>
<html lang="en">
<head>
<meta charset="utf-8">
<title>Vexar Energy – Pink Lemonade Label</title>
<link rel="stylesheet" href="https://fonts.googleapis.com/css2?family=Orbitron:wght@500;700;900&display=swap">
<style>
  :root {
    --canvas: #000000;
    --label-base: #150a1a;
    --brand-red: #d8232e;
    --silver: #c9ccd6;
    --white: #f2f2f5;
    --rule: #a9acb8;
    --net-red: #e0262e;
  }
  * { margin: 0; padding: 0; box-sizing: border-box; }
  html, body {
    width: 1200px; height: 1200px; overflow: hidden;
    background: var(--canvas);
    font-family: "Orbitron", sans-serif;
  }
  .label {
    position: absolute; left: 200px; top: 330px;
    width: 800px; height: 660px; overflow: hidden;
    background: var(--label-base);
  }
  .label-art {
    position: absolute; inset: 0;
    background:
      radial-gradient(ellipse 150px 80px at 290px 330px, rgba(255,196,138,0.9), rgba(255,196,138,0) 70%),
      radial-gradient(ellipse 300px 160px at 270px 350px, rgba(232,52,106,0.8), rgba(232,52,106,0) 72%),
      radial-gradient(ellipse 380px 220px at 420px 420px, rgba(176,42,140,0.5), rgba(176,42,140,0) 75%),
      radial-gradient(ellipse 300px 260px at 680px 200px, rgba(106,43,176,0.45), rgba(106,43,176,0) 75%),
      linear-gradient(160deg, #1a0d22 0%, #241033 50%, #120818 100%);
  }
  .tagline {
    position: absolute; left: 140px; top: 62px; width: 350px;
    color: var(--white); font-weight: 700; font-size: 12px;
    letter-spacing: 1.5px; line-height: 16px; text-align: center;
  }
  .tagline sup { font-size: 7px; letter-spacing: 0; }
  .rule { position: absolute; left: 172px; width: 286px; height: 3px; background: var(--rule); }
  .rule.top { top: 98px; }
  .rule.bottom { top: 127px; }
  .maker {
    position: absolute; left: 172px; top: 103px; width: 286px;
    color: var(--silver); font-weight: 700; font-size: 18px;
    letter-spacing: 2.5px; text-align: center; line-height: 22px;
  }
  .brand-name { color: var(--brand-red); font-weight: 900; line-height: 1; }
  .brand-name .word-main {
    position: absolute; left: 100px; top: 121px;
    font-size: 140px; letter-spacing: 2px;
  }
  .brand-name .word-sub {
    position: absolute; left: 452px; top: 254px;
    font-size: 42px; letter-spacing: 1px;
  }
  .facts {
    position: absolute; left: 417px; width: 300px;
    text-align: center; color: var(--white); line-height: 1;
  }
  .flavor { top: 322px; font-size: 21px; font-weight: 700; letter-spacing: 3px; }
  .claim-big { font-size: 33px; font-weight: 900; color: var(--silver); letter-spacing: 1px; }
  .claim-small { font-size: 14px; font-weight: 700; letter-spacing: 2px; margin-top: 4px; }
  .zero { top: 372px; }
  .sugar { top: 424px; }
  .servings { top: 474px; left: 372px; }
  .servings .count { font-size: 62px; font-weight: 900; color: var(--silver); letter-spacing: 4px; }
  .servings .claim-small { font-size: 16px; margin-top: 6px; }
  .legal { top: 566px; left: 436px; width: 180px; text-align: left; }
  .legal .kind { font-size: 8px; font-weight: 700; letter-spacing: 1px; }
  .legal .weight { font-size: 8px; font-weight: 700; letter-spacing: 1px; color: var(--net-red); margin-top: 3px; }
</style>
</head>
<body>
  <main class="label">
    <div class="label-art" role="img" aria-label="Glowing pink, orange and violet energy wave swirl across a dark background"></div>

    <p class="tagline">THE MOST POWERFUL<br>ENERGY DRINK IN GAMING<sup>TM</sup></p>
    <div class="rule top"></div>
    <p class="maker">APEXION LABS</p>
    <div class="rule bottom"></div>

    <h1 class="brand-name">
      <span class="word-main">VEXAR</span>
      <span class="word-sub">ENERGY</span>
    </h1>

    <p class="facts flavor">PINK LEMONADE</p>

    <div class="facts zero">
      <div class="claim-big">ZERO</div>
      <div class="claim-small">CALORIES</div>
    </div>
    <div class="facts sugar">
      <div class="claim-big">NO</div>
      <div class="claim-small">SUGAR</div>
    </div>
    <div class="facts servings">
      <div class="count">30</div>
      <div class="claim-small">SERVINGS</div>
    </div>
    <div class="facts legal">
      <div class="kind">DIETARY SUPPLEMENT</div>
      <div class="weight">NET WT. 0.0OZ (000G)</div>
    </div>
  </main>
</body>
</html>
```